Online Advice via Video Site requires Cutting Edge Homepage

We need a creative new and exciting webdesign for our tutoring via video-chat website.

We have prepared a "demo" homepage for you to see various promotional material that we think would be suitable for the homepage. http://www.quillmarsh.com/demo

The actual site is undergoing some final tinkering but can be accessed and used at http://www.quillmarsh.com

There is NO NEED to take any colours or design structure from this.

We expect the logo to be changed to match the new site. The new logo should match the site's function.

I have included some other projects that we like the look of:
http://www.vantoplex.com.au/design/143762
http://www.vantoplex.com.au/design/561630
http://www.vantoplex.com.au/design/247199
http://www.vantoplex.com.au/design/255195
http://www.birchlume.tv/

Target Market(s)

People that will work as tutors/advisers or be student/clients

Industry/Entity Type

Tutoring

Requirements
Must have
• The search is the main feature of the homepage

After the search the next goal of the page is to get people to sign up to the site

Login, (optional inclusion of the gablenet login - if you don't include it then you need only have a "login" button... no username or password input fields)

Footer
Nice to have
• The promotional material for the site, the colours on the Prezi file CAN BE changed to suit the new design you propose.

```html
<!DOCTYPE html>
<html lang="en">
<head>
<meta charset="utf-8">
<title>Quill Marsh — Online Advice</title>
<link rel="stylesheet" href="https://fonts.googleapis.com/css2?family=Source+Sans+3:ital,wght@0,300;0,400;0,600;1,400&display=swap">
<style>
:root{
  --ink:#3d3d3d;
  --muted:#666;
  --dark:#2b2b2b;
  --brand:#3f5ea6;
  --brand-deep:#3a5aa2;
  --accent:#4470d4;
  --accent-soft:#5a7fc6;
  --band:#d3dcf5;
  --tab:#dcdfe3;
  --tab-active:#e9eef0;
  --panel:#f3f3f3;
  --line:#c9c9c9;
  --white:#fff;
}
*{box-sizing:border-box;margin:0;padding:0}
html,body{width:1145px;height:1200px;overflow:hidden;background:var(--white)}
body{font-family:"Source Sans 3",Arial,sans-serif;color:var(--ink)}
.stage{position:relative;width:1050px;height:1100px;transform:scale(1.0905);transform-origin:0 0;overflow:hidden}
.abs{position:absolute}
ul{list-style:none}

/* top bar */
.topbar{left:0;top:0;width:1050px;height:64px;background:var(--dark)}
.social-login{left:470px;top:13px;width:159px;height:24px;background:#4a77c0;border:1px solid #6a92d4;border-radius:2px;color:var(--white);font-size:11px;line-height:22px}
.social-login .mark{position:absolute;left:0;top:0;width:24px;height:22px;border-right:1px solid #6a92d4}
.social-login span.label{position:absolute;left:40px}
.field{height:24px;background:var(--white);border:1px solid #bbb;border-radius:2px;color:#aaa;font-style:italic;font-size:11px;line-height:22px;padding-left:8px}
.user{left:665px;top:13px;width:129px}
.pass{left:799px;top:13px;width:129px}
.login-btn{left:934px;top:13px;width:64px;height:24px;background:#4a7ad0;border:1px solid #7aa0e0;border-radius:2px;color:var(--white);font-size:12px;line-height:22px;text-align:right;padding-right:5px}
.login-btn svg{position:absolute;left:6px;top:3px}
.forgot{left:849px;top:43px;color:#ccc;font-size:10px;font-style:italic;text-decoration:underline}

/* header */
.header{left:0;top:64px;width:1050px;height:294px;background:linear-gradient(180deg,#3b5aa0,#4565b0 60%,#4161aa)}
.logo{left:43px;top:82px;color:var(--white);font-size:38px;font-weight:300;letter-spacing:.5px}
.connect{left:727px;top:97px;color:var(--white);font-size:13px}
.connect-icons{left:828px;top:92px;display:flex;gap:7px}
.connect-icons span{width:28px;height:28px;border-radius:3px;background:#d8def0;border:1px solid #fff}
.nav{left:55px;top:151px;display:flex;gap:3px}
.nav a{display:block;height:32px;padding:0 12px;line-height:32px;background:var(--tab);color:#555;font-size:13px;text-decoration:none;border-radius:2px 2px 0 0}
.nav a.active{background:var(--tab-active);color:#333;width:70px;text-align:center}

.band{left:0;top:358px;width:1050px;height:60px;background:var(--band)}
.adv-link{left:819px;top:381px;font-size:11px;color:#555;text-decoration:underline}
.search-btn{left:918px;top:376px;width:66px;height:25px;background:#4a78d4;border-radius:3px;color:var(--white);font-size:15px;line-height:24px;text-align:center}

/* hero */
.hero{left:43px;top:183px;width:646px;height:310px;background:var(--white);box-shadow:0 3px 6px rgba(0,0,0,.3)}
.hero-photo{left:6px;top:6px;width:634px;height:298px;background:linear-gradient(90deg,#f3f5f8 0%,#e8edf2 45%,#c9d3dc 75%,#aab8c6 100%)}
.quote{left:43px;top:72px;width:360px;font-size:16.5px;line-height:22px;color:#4a4a4a}
.quote .strong{display:block;margin-top:4px;font-size:22px;color:var(--accent)}
.slider-ctrl{left:12px;top:276px;width:35px;height:21px;background:#777;border-radius:2px}

/* search panel */
.search-panel{left:703px;top:183px;width:296px;height:160px;background:#f0f0f0;box-shadow:0 1px 3px rgba(0,0,0,.3)}
.search-inner{left:6px;top:6px;width:284px;height:148px;background:var(--white)}
.search-title{left:56px;top:20px;font-size:18px;color:var(--accent)}
.search-panel svg.mag{position:absolute;left:16px;top:20px}
.checks{left:23px;top:66px;display:flex;gap:16px;font-size:11px;color:#666}
.checks span::before{content:"";display:inline-block;width:8px;height:8px;border:1px solid #aaa;background:#eee;margin-right:6px;vertical-align:-1px}
.search-input{left:14px;top:97px;width:268px;height:32px;border:1px solid #c9c9c9;border-radius:4px;background:linear-gradient(#e4e4e4,#f4f4f4)}

/* welcome */
.welcome-title{left:43px;top:517px;font-size:22px;font-weight:400;color:var(--accent)}
.welcome-text{left:43px;top:553px;width:647px;font-size:12.5px;line-height:17.6px;text-align:justify;color:#555}
.points{left:97px;top:657px}
.points li{position:relative;height:31px;padding-left:19px;font-size:15px;font-style:italic;color:var(--accent-soft)}
.points li::before{content:"";position:absolute;left:0;top:5px;border-left:7px solid #6a8fd6;border-top:5px solid transparent;border-bottom:5px solid transparent}

/* advisors panel */
.adv-panel{left:710px;top:443px;width:282px;height:326px;background:#ececec;box-shadow:0 1px 3px rgba(0,0,0,.25)}
.adv-inner{left:7px;top:6px;width:268px;height:312px;background:var(--white)}
.adv-icon{left:20px;top:12px;width:28px;height:28px;border-radius:50%;background:#c9d0dc}
.adv-title{left:58px;top:14px;font-size:18px;color:var(--accent)}
.adv-list{left:14px;top:64px;font-size:12px;color:#444;line-height:22px}
.adv-list li::before{content:"•";color:#999;margin-right:6px}
.adv-list li.sub{padding-left:27px}
.adv-list li.sub.tight{padding-left:27px;margin-left:-4px}

/* bottom panel */
.lower{left:0;top:797px;width:1050px;height:243px;background:var(--panel);border-top:2px solid #4a6fd0}
.ftabs{left:42px;top:0;display:flex;font-size:13px;color:#555}
.ftabs span{height:32px;line-height:32px;padding:0 8px;margin-right:16px}
.ftabs span.on{background:#4a74d4;color:var(--white);padding:0 12px;margin-right:0}
.fpoints{font-size:13px;color:#444;line-height:32px}
.fpoints li::before{content:"•";color:#888;margin-right:8px}
.rule{left:42px;top:123px;width:645px;height:1px;background:var(--line)}
.topic-tag{left:52px;top:148px;width:108px;height:73px;background:#4a74d4;color:var(--white);font-size:12px;line-height:16px;text-align:center;padding-top:20px}
.topic-tag::after{content:"";position:absolute;right:-11px;top:28px;border-left:11px solid #4a74d4;border-top:9px solid transparent;border-bottom:9px solid transparent}
.topics{font-size:13px;color:#444}
.vrule{left:703px;top:11px;width:2px;height:219px;background:#d0d0d0}
.testi-title{left:757px;top:10px;font-size:18px;color:var(--accent)}
.testi-icon{left:718px;top:8px}
.testi{left:719px;width:266px;font-size:12px;font-style:italic;line-height:18px;color:#555}
.testi .q{font-size:16px;color:#777}
.testi .who{display:block;text-align:right;font-style:normal;font-weight:600;color:#444;margin-top:8px;font-size:12.5px}

.footer{left:0;top:1040px;width:1050px;height:60px;background:var(--dark);color:#bdbdbd;font-size:11.5px;text-align:center;line-height:58px}
</style>
</head>
<body>
<div class="stage">

  <div class="abs topbar">
  </div>
  <div class="abs social-login"><span class="mark"></span><span class="label">sign in with gablenet</span></div>
  <div class="abs field user">Username</div>
  <div class="abs field pass">Password</div>
  <div class="abs login-btn">
    <svg width="16" height="16" viewBox="0 0 16 16"><circle cx="8" cy="5" r="4" fill="#223"/><path d="M1 16c0-5 3-7 7-7s7 2 7 7z" fill="#223"/></svg>
    Log in
  </div>
  <a class="abs forgot">Forgot password</a>

  <header class="abs header"></header>
  <div class="abs logo">Quill Marsh</div>
  <div class="abs connect">Connect with us :</div>
  <div class="abs connect-icons"><span></span><span></span><span></span><span></span></div>
  <nav class="abs nav">
    <a class="active">Home</a><a>About us</a><a>Our Services</a><a>Advisors</a><a>Testimonials</a><a>Contact us</a>
  </nav>

  <div class="abs band"></div>
  <a class="abs adv-link">Advanced Search</a>
  <div class="abs search-btn">Search</div>

  <section class="abs hero">
    <div class="abs hero-photo" role="img" aria-label="Photo of a woman with outstretched arms on a bright beach"></div>
    <p class="abs quote">"Imagine if, whenever you had a problem you could instantly access the world's experts to solve it.<span class="strong">Now you can!"</span></p>
    <div class="abs slider-ctrl">
      <svg width="35" height="21" viewBox="0 0 35 21"><path d="M14 5 8 10.5 14 16z" fill="#fff"/><path d="M21 5 27 10.5 21 16z" fill="#fff"/><rect x="17" y="3" width="1" height="15" fill="#999"/></svg>
    </div>
  </section>

  <section class="abs search-panel">
    <div class="abs search-inner">
      <svg class="mag" width="30" height="26" viewBox="0 0 30 26"><circle cx="11" cy="10" r="8" fill="#e8eef6" stroke="#8a9ab0" stroke-width="2"/><path d="M17 15 27 23" stroke="#556" stroke-width="4" stroke-linecap="round"/></svg>
      <h2 class="abs search-title" style="font-weight:400">Search</h2>
      <div class="abs checks"><span>Topics</span><span>Advisors</span></div>
      <div class="abs search-input"></div>
    </div>
  </section>

  <h1 class="abs welcome-title">Welcome to our site</h1>
  <p class="abs welcome-text">Sed ut perspiciatis unde omnis iste natus error sit voluptatem accusantium doloremque laudantium, totam rem aperiam, eaque ipsa quae ab illo inventore veritatis et quasi architecto beatae vitae dicta sunt explicabo. Nemo enim ipsam voluptatem quia voluptas sit aspernatur aut odit aut fugit, sed quia consequuntur magni dolores eos qui ratione voluptatem sequi nesciunt. Neque porro quisquam est, qui dolorem ipsum quia dolor sit amet, consectetur, adipisci velit, sed quia non numquam eius modi tempora incidunt ut laboreet.</p>
  <ul class="abs points">
    <li>QuillMarsh is the place for e-learning, mentoring &amp; professional advice</li>
    <li>It instantly connects people with knowledge and those who need it</li>
    <li>Connects people for ongoing advice or on off answers</li>
    <li>Ask questions and/or work exactly when it suits you</li>
  </ul>

  <aside class="abs adv-panel">
    <div class="abs adv-inner">
      <div class="abs adv-icon"></div>
      <h2 class="abs adv-title" style="font-weight:400">Advisors</h2>
      <ul class="abs adv-list">
        <li>Teach the topics you know well</li>
        <li>Educate people in your spare time</li>
        <li class="sub">Answer single questions</li>
        <li class="sub tight">Provide ongoing tutoring</li>
        <li>Work when it suits you</li>
        <li class="sub">Pre-book appointments</li>
        <li class="sub">Answer questions only when you can</li>
        <li>Earn money for your time</li>
        <li class="sub">Set your own fee rate</li>
      </ul>
    </div>
  </aside>

  <section class="abs lower">
    <div class="abs ftabs">
      <span>Instant Personal Advice</span><span>Direct Video Conference</span><span>Advisors and/or Clients</span><span class="on">Payvine or Credt Card</span>
    </div>
    <ul class="abs fpoints" style="left:89px;top:41px"><li>Charges based on individual advisor's rate</li><li>Pay via payvine or credit card</li></ul>
    <ul class="abs fpoints" style="left:416px;top:41px"><li>Pay only for the time you use</li><li>Be paid via credit card</li></ul>
    <div class="abs rule"></div>
    <div class="abs topic-tag">ADVISORS<br>BY TOPICS</div>
    <span class="abs topics" style="left:193px;top:157px">English</span>
    <span class="abs topics" style="left:297px;top:157px">Building</span>
    <span class="abs topics" style="left:432px;top:157px">Cultural Studies</span>
    <span class="abs topics" style="left:598px;top:157px">Criminology</span>
    <span class="abs topics" style="left:193px;top:187px">Agriculture</span>
    <span class="abs topics" style="left:294px;top:187px">Veterinary Science</span>

    <div class="abs vrule"></div>
    <svg class="abs testi-icon" width="26" height="30" viewBox="0 0 26 30"><rect x="3" y="3" width="18" height="24" fill="#fff" stroke="#999"/><path d="M7 10h10M7 14h10M7 18h8" stroke="#aaa"/><path d="M14 22 24 4" stroke="#557" stroke-width="2"/></svg>
    <h2 class="abs testi-title" style="font-weight:400">Testimonials</h2>
    <p class="abs testi" style="top:60px"><span class="q">“</span> Neque porro quisquam est, qui dolorem ipsum quia dolor sit amet, consectetur, adipisci velit, sed quia non numquam eius modi <span class="q">”</span><span class="who">David</span></p>
    <p class="abs testi" style="top:150px"><span class="q">“</span> Neque porro quisquam est, qui dolorem ipsum quia dolor sit amet, consectetur, adipisci velit, sed quia non numquam eius modi <span class="q">”</span><span class="who">David</span></p>
  </section>

  <footer class="abs footer">Copyright &nbsp;© 2012 www.quillmarsh.com &nbsp; All rights reserved</footer>
</div>
</body>
</html>
```